RWT Fittings Ltd Business Cards

We need a business card with our business logo. We provide window and door installations on high-rises in west coast British Colombia, Canada.

I would like my business information and details on one side of the card, and the other side the company name with logo

Target Market(s)

General Contractors

Industry/Entity Type

Construction

Contact Information for Business Card

one side i want my company name and logo in the dark theme logo that i provided

Requirements
Must have
• Marco Peltieri, 16045518293, RWTFittings@mailbox-demo.com, 1407-5194 Linden Row Burnaby BC, V5H 2K9, Owner & Manager

```html
<!DOCTYPE html>
<html lang="en">
<head>
<meta charset="utf-8">
<title>RWT Fittings Ltd – Business Cards</title>
<link rel="stylesheet" href="https://fonts.googleapis.com/css2?family=Montserrat:wght@400;600;700&family=Lato:wght@400;700&display=swap">
<style>
  :root {
    --stage: #2b2d30;
    --stage-light: #3a3d41;
    --card-white: #ffffff;
    --card-dark: #3b3b3d;
    --brand-blue: #27a8e0;
    --ink: #3d3d3f;
    --ink-soft: #6a6a6d;
  }
  * { margin: 0; padding: 0; box-sizing: border-box; }
  html, body { width: 1200px; height: 952px; overflow: hidden; }
  body {
    background: radial-gradient(ellipse at 60% 40%, var(--stage-light), var(--stage) 70%);
    font-family: "Lato", Arial, sans-serif;
    position: relative;
  }
  .card {
    position: absolute;
    top: 321px;
    width: 540px;
    height: 310px;
    border-radius: 22px;
    overflow: hidden;
    box-shadow: 0 14px 30px rgba(0,0,0,.45);
  }
  .card-front { left: 40px; background: var(--card-white); }
  .card-back { left: 620px; background: var(--card-dark); }

  .wordmark {
    display: flex;
    align-items: center;
    gap: 10px;
    font-family: "Montserrat", Arial, sans-serif;
    font-weight: 700;
    color: var(--brand-blue);
    white-space: nowrap;
  }
  .wordmark-square { background: var(--brand-blue); flex: none; }

  .card-front .wordmark { position: absolute; top: 34px; left: 150px; font-size: 22px; }
  .card-front .wordmark-square { width: 18px; height: 18px; }

  .contact-band {
    position: absolute;
    left: 0; top: 112px;
    width: 270px; height: 150px;
    background: var(--brand-blue);
    padding: 18px 0 0 22px;
    color: #fff;
    font-size: 12.5px;
    line-height: 1.35;
  }
  .contact-item { display: flex; align-items: flex-start; gap: 9px; margin-bottom: 6px; }
  .contact-icon {
    width: 15px; height: 15px; flex: none;
    background: #fff; border-radius: 3px;
    display: flex; align-items: center; justify-content: center;
    margin-top: 1px;
  }
  .contact-icon svg { width: 11px; height: 11px; fill: var(--brand-blue); }
  .contact-address { position: absolute; left: 22px; top: -34px; color: var(--ink); display: flex; gap: 9px; }
  .contact-address .contact-icon { background: var(--brand-blue); }
  .contact-address .contact-icon svg { fill: #fff; }

  .person { position: absolute; left: 300px; top: 150px; }
  .person-name {
    font-family: "Montserrat", Arial, sans-serif;
    font-size: 22px;
    color: var(--brand-blue);
    letter-spacing: .5px;
    font-weight: 400;
  }
  .person-name strong { font-weight: 700; }
  .person-title { font-size: 14px; color: var(--ink-soft); margin-top: 4px; padding-left: 70px; }

  .card-back .wordmark { position: absolute; top: 50%; left: 50%; transform: translate(-50%, -50%); font-size: 34px; gap: 14px; }
  .card-back .wordmark-square { width: 26px; height: 26px; }
</style>
</head>
<body>

<section class="card card-front" aria-label="Business card front">
  <div class="wordmark"><span class="wordmark-square"></span>RWT Fittings Ltd</div>

  <div class="contact-band">
    <div class="contact-address">
      <span class="contact-icon"><svg viewBox="0 0 12 12"><path d="M6 0a4 4 0 0 0-4 4c0 3 4 8 4 8s4-5 4-8a4 4 0 0 0-4-4zm0 5.6A1.6 1.6 0 1 1 6 2.4a1.6 1.6 0 0 1 0 3.2z"/></svg></span>
      <span>1407-5194 Linden Row<br>Burnaby BC, V5H 2K9</span>
    </div>
    <div class="contact-item">
      <span class="contact-icon"><svg viewBox="0 0 12 12"><path d="M2.4 0.6l2 2-1 1.4a7 7 0 0 0 4.6 4.6l1.4-1 2 2-1.4 1.8C5 11 1 7 .6 2z"/></svg></span>
      <span>16045518293</span>
    </div>
    <div class="contact-item">
      <span class="contact-icon"><svg viewBox="0 0 12 12"><path d="M0 2h12v8H0zm1 1v.4l5 3.2 5-3.2V3zm0 1.6V9h10V4.6L6 7.8z"/></svg></span>
      <span>RWTFittings@mailbox-demo.com</span>
    </div>
    <div class="contact-item">
      <span class="contact-icon"><svg viewBox="0 0 12 12"><path d="M6 0a6 6 0 1 0 0 12A6 6 0 0 0 6 0zm0 1.2c.6 0 1.3 1.2 1.6 3.2H4.4C4.7 2.4 5.4 1.2 6 1.2zM1.3 5.6h2.9v.8H1.3zm6.5 0h2.9v.8H7.8zM4.4 7.6h3.2C7.3 9.6 6.6 10.8 6 10.8S4.7 9.6 4.4 7.6z"/></svg></span>
      <span>www.rwtfittings-demo.com</span>
    </div>
  </div>

  <div class="person">
    <p class="person-name">MARCO <strong>PELTIERI</strong></p>
    <p class="person-title">Owner &amp; Manager</p>
  </div>
</section>

<section class="card card-back" aria-label="Business card back">
  <div class="wordmark"><span class="wordmark-square"></span>RWT Fittings Ltd</div>
</section>

</body>
</html>
```